Sandwich Board and Poster design promoting a medical aesthetic clinic

I am looking for a clean, modern and relaxing design promoting a medical physician-led aesthetic clinic.
Services offered are neuromodulator treatment (Dyneline) and Dermal Fillers.
Logo must be included.
Use the tag line "Refresh your look, revive your spirit."
Address is 204-205 27361 93 Ave, Surrey, K7P 2R4
604-555-0172
email - info@brightmoorskin.ca
www.brightmoorskin.ca

```html
<!DOCTYPE html>
<html lang="en">
<head>
<meta charset="utf-8">
<title>Brightmoor Rejuvenation – Poster</title>
<link rel="stylesheet" href="https://fonts.googleapis.com/css2?family=Montserrat:wght@500;900&family=Roboto+Condensed:wght@700&family=Arimo:wght@400;700&display=swap">
<style>
  :root {
    --backdrop: #8a7770;
    --paper: #f8f8f8;
    --sky-light: #b9e6f0;
    --sky-deep: #19b4dc;
    --skin: #c99478;
    --hair: #4a3426;
    --towel: #eef1f3;
    --ink: #1b1b1b;
    --headline: #7c6a64;
    --bar: #0a0a0a;
    --bar-text: #ffffff;
    --phone: #a99c97;
    --dots: #8d7d78;
  }
  * { margin: 0; padding: 0; box-sizing: border-box; }
  html, body { width: 1200px; height: 840px; overflow: hidden; }
  body {
    background: var(--backdrop);
    display: flex;
    align-items: center;
    justify-content: center;
  }
  .poster {
    position: relative;
    width: 570px;
    height: 800px;
    background: var(--paper);
    overflow: hidden;
    box-shadow: 0 6px 24px rgba(0,0,0,.18);
  }
  .hero {
    position: absolute;
    inset: 0 0 auto 0;
    width: 570px;
    height: 570px;
    display: block;
  }
  .brand {
    position: absolute;
    top: 128px;
    left: 0;
    width: 100%;
    text-align: center;
    font-family: "Montserrat", sans-serif;
    font-weight: 500;
    color: var(--ink);
  }
  .brand-name { font-size: 32px; letter-spacing: 9px; line-height: 1; padding-left: 9px; }
  .brand-sub { font-size: 10px; letter-spacing: 6px; margin-top: 7px; padding-left: 6px; }
  .tagline {
    position: absolute;
    left: 73px;
    top: 608px;
    font-family: "Montserrat", sans-serif;
    font-weight: 900;
    font-size: 37px;
    line-height: 35px;
    letter-spacing: -1.2px;
    color: var(--headline);
  }
  .divider {
    position: absolute;
    left: 73px;
    top: 693px;
    width: 415px;
    border-top: 1.5px dotted var(--dots);
  }
  .services {
    position: absolute;
    left: 73px;
    top: 703px;
    font-family: "Arimo", sans-serif;
    font-size: 12.3px;
    color: var(--ink);
    letter-spacing: .1px;
  }
  .contact-bar {
    position: absolute;
    left: 57px;
    bottom: 0;
    width: 453px;
    height: 52px;
    background: var(--bar);
    display: flex;
    align-items: center;
    justify-content: space-between;
    padding: 0 16px 0 18px;
  }
  .contact-lines { font-family: "Arimo", sans-serif; color: var(--bar-text); }
  .address { font-weight: 700; font-size: 9.4px; letter-spacing: .1px; }
  .links { font-size: 7.6px; margin-top: 3px; letter-spacing: .3px; display: flex; gap: 5px; align-items: center; }
  .links .dot { width: 5px; height: 5px; border-radius: 50%; border: 1px solid var(--bar-text); display: inline-block; margin-right: 2px; }
  .phone {
    font-family: "Roboto Condensed", sans-serif;
    font-weight: 700;
    font-size: 29px;
    color: var(--phone);
    letter-spacing: .2px;
  }
</style>
</head>
<body>
  <article class="poster">
    <svg class="hero" viewBox="0 0 570 570" role="img" aria-label="Photo of a woman lying on a towel with eyes closed while gloved hands give a forehead injection, against a soft blue sky">
      <defs>
        <radialGradient id="sky" cx="0.42" cy="0.18" r="0.9">
          <stop offset="0" stop-color="#e4f6fa"/>
          <stop offset="0.45" stop-color="var(--sky-light)"/>
          <stop offset="1" stop-color="var(--sky-deep)"/>
        </radialGradient>
        <linearGradient id="scene" x1="0" y1="0" x2="1" y2="0.2">
          <stop offset="0" stop-color="var(--towel)"/>
          <stop offset="0.3" stop-color="var(--hair)"/>
          <stop offset="0.55" stop-color="var(--skin)"/>
          <stop offset="0.85" stop-color="#d9a98e"/>
          <stop offset="1" stop-color="var(--towel)"/>
        </linearGradient>
        <clipPath id="arc">
          <path d="M0,0 H570 V440 C520,520 420,562 290,562 C160,562 50,510 0,415 Z"/>
        </clipPath>
      </defs>
      <g clip-path="url(#arc)">
        <rect width="570" height="570" fill="url(#sky)"/>
        <path d="M0,560 L0,380 C90,360 180,420 260,400 C340,360 420,330 570,400 L570,570 Z" fill="url(#scene)" opacity=".9"/>
      </g>
    </svg>

    <header class="brand">
      <div class="brand-name">BRIGHTMOOR</div>
      <div class="brand-sub">REJUVENATION</div>
    </header>

    <h1 class="tagline">REFRESH YOUR LOOK,<br>REVIVE YOUR SPIRIT.</h1>
    <div class="divider"></div>
    <p class="services">NEUROMODULATOR TREATMENT (DYNELINE)" AND "DERMAL FILLERS.</p>

    <footer class="contact-bar">
      <div class="contact-lines">
        <div class="address">204-205 27361 93 AVE, SURREY, K7P 2R4</div>
        <div class="links">
          <span><i class="dot"></i>info@brightmoorskin.ca</span>
          <span><i class="dot"></i>www.brightmoorskin.ca</span>
        </div>
      </div>
      <div class="phone">604-555-0172</div>
    </footer>
  </article>
</body>
</html>
```